Website Redesign Project

Brightwater Delivery Partners provides project management and project controls consultancy services to companies in many industry sectors, within Australia and overseas. My company has been developing a business brand through forging strong business relationships within industry. We provide innovative tools, concepts and solutions to management teams to assist them in better plan and managing there project portfolios.
SECTORS OF INDUSTRY WE SERVICE
★Oil & Gas
★Minerals & Metals
★Petrochemical
★Manufacturing
★Building & Construction
★Telecommunications
★Rail
★Civil
OLD WEBSITE
My old website www.brightwaterdeliverypartners-demo.com.au needs a complete overhaul in terms of how the web pages look and feel. I am trying to get away from the grey, washed out look as it is uninviting and dull. My clients commented that my webpage does not reflect who I am as a company or my core values. Think total redesign
DESIGN
I would like a webpage design that is modern and has a corporate image. It must be elegant, classy, and have an overall glossy appearance. I want something exciting that creates some excellent feedback from clients. It needs to have a savvy appearance and an attitude of a market leader. A generic website template cannot be used as I provide a unique service to clients. I do not need a website design that looks like my compeditors, I want something that stands out in the crowd and effectivly markets my bussinesses brand. I want my website to represent quality, so only high resolution images that are clear, sharp and in focus can be used. With this design, throw your standard webpage design concepts out the window, as I want something fresh, innovative, exciting and inviting. The overall design should appear uncluttered as all content needs to be there for a reason, so think functional.
It must be professional and of the highest calibre as my clients expect nothing less. I provide clients with innovative tools, concepts and solutions, so the design needs to be edgy and creative to align with my company’s core business services. The new design must promote the company’s brand and us as a market leader. It must communicate that we service many industry sectors and reflect our company’s creativity, vision, energy and drive.
WEBPAGE WRITTEN CONTENT
I am happy with the written content on each page within my old website. You may arrange the text how you see fit within the new design. On the main page of my old website the text is under scored, I am not a big fan of this. I currently do not like the format the text is in, I am looking for a formatt that is easy to read, looks flattering and pleasing to the eye.
MAIN PAGE DESIGN
The main page design needs to focus on my company as a brand, it must promote that I service many industry sectors. My old webpage had me pigeon holed as only providing services to oil and gas. This is incorrect as I service oil & gas, metals and minerals, Petrochemical, Manufacturing, Building & Construction, Telecommunications, Rail and civil.
WEBPAGE COLUR PREFERENCE
Prefer a white background with plenty of colour
TESTIMONIAL TAB
The testimonial tab on the task bar can be removed as it is no longer required.
FINISHED PRODUCT
The finished product will be uploaded by you to a nominated web hosting account. I will need a copy of all files associated with the design. A copy of the finished product will also be provided in formats that can me imported to Xara Pro Designer as I will update my website in 6 months or so using this tool.
Updates
I have updated the design brief after recieving feedback from several designers
Thanks
Reason: Some designers have asked for more time
Hi All
I have just launched another project called "brightwater delivery partners business card redesign project", you are all welcome to join this project.
Thanks
Target Market(s)
★Oil and Gas
★Mining and Resources
★Building and infrastructure
★Petrochemical
★Civil and roads
★Rail
Industry/Entity Type
Industry
Requirements
Must have
- ★Draw you in
★Hold your attention
★Identify company brand
★Highlight skills experience and expertise
★Be a unique design not generic
Should not have
- ★The webpage design should not be old fashioned
★ The design should not be based off a generic design template
★The webpage should not be cluttered; everything needs to be there for a reason.

```html
<!DOCTYPE html>
<html lang="en">
<head>
<meta charset="utf-8">
<title>Brightwater Delivery Partners</title>
<link href="https://fonts.googleapis.com/css2?family=Open+Sans:wght@400;600;700;800&display=swap" rel="stylesheet">
<style>
:root{
  --red:#c4161c;
  --red-dark:#8e0d12;
  --red-deep:#a51218;
  --ink:#1d1d1d;
  --grey:#6b6b6b;
  --line:#e2e2e2;
  --white:#ffffff;
  --footer:#1f1f1f;
  --footer-deep:#151515;
}
*{margin:0;padding:0;box-sizing:border-box}
html,body{width:828px;height:1200px;overflow:hidden}
body{position:relative;background:var(--white);font-family:"Open Sans",Arial,sans-serif;color:var(--ink)}

/* header */
.site-header{position:absolute;left:0;top:0;width:828px;height:84px;background:var(--white)}
.brand{position:absolute;left:16px;top:16px;display:flex;align-items:center;gap:8px}
.brand-dot{width:30px;height:30px;border-radius:50%;background:var(--red)}
.brand-name{font-size:20px;font-weight:800;color:var(--ink);letter-spacing:-.3px;line-height:1}
.brand-tag{position:absolute;left:54px;top:42px;font-size:7.5px;color:var(--grey);font-style:normal}
.contact{position:absolute;right:16px;top:14px;text-align:left}
.contact-row{display:flex;align-items:center;gap:7px;color:var(--ink)}
.contact-row.phone{font-size:17px;font-weight:600;margin-bottom:5px}
.contact-row.mail{font-size:8.5px;color:var(--grey)}
.contact-row svg{flex:none}

/* nav */
.main-nav{position:absolute;left:0;top:84px;width:828px;height:21px;background:linear-gradient(#d21c22,var(--red-deep));display:flex;padding-left:86px}
.main-nav a{display:block;height:21px;line-height:21px;padding:0 13px;color:var(--white);font-size:8.5px;font-weight:600;text-decoration:none;text-transform:uppercase;border-right:1px solid rgba(255,255,255,.18)}
.main-nav a.active{background:var(--footer-deep)}

/* hero */
.hero{position:absolute;left:0;top:105px;width:828px;height:347px;background:linear-gradient(180deg,#20324f 0%,#3d5b86 38%,#6a7fa0 62%,#c98a5a 82%,#2a3040 100%)}
.hero-copy{position:absolute;left:470px;top:92px;width:330px;color:var(--white)}
.hero-copy h2{font-size:13.5px;font-weight:700;text-transform:uppercase;margin-bottom:10px;letter-spacing:.2px}
.hero-copy p{font-size:8.5px;line-height:1.45;color:#e6ebf2}
.hero-arrow{position:absolute;top:283px;width:26px;height:26px;border-radius:50%;background:rgba(20,20,20,.75);display:flex;align-items:center;justify-content:center}
.hero-arrow.prev{left:34px}
.hero-arrow.next{right:34px}

/* red zone */
.content-zone{position:absolute;left:0;top:452px;width:828px;height:624px;background:linear-gradient(180deg,var(--red) 0%,#b3141a 100%)}
.panel{position:absolute;left:33px;width:762px;background:var(--white);box-shadow:0 2px 6px rgba(0,0,0,.25)}
.panel.intro{top:23px;height:190px}
.panel.sectors{top:238px;height:372px}

.welcome{position:absolute;left:18px;top:16px;width:500px}
.welcome h1{font-size:14px;font-weight:700;color:var(--ink);padding-bottom:6px;border-bottom:1px solid var(--line);margin-bottom:10px}
.welcome h1 span{color:var(--red);text-transform:uppercase}
.welcome p{font-size:8.5px;line-height:1.55;color:var(--grey);margin-bottom:9px}
.btn-more{position:absolute;height:16px;padding:0 10px;background:var(--red-dark);color:var(--white);font-size:7.5px;font-weight:700;line-height:16px;text-transform:uppercase;border-radius:2px}
.welcome .btn-more{right:0;top:150px}

.expertise{position:absolute;left:540px;top:16px;width:205px}
.expertise h3{font-size:13px;font-weight:700;color:var(--ink);padding-bottom:6px;border-bottom:2px solid var(--red);margin-bottom:8px}
.expertise ul{list-style:none}
.expertise li{font-size:7.5px;color:var(--grey);line-height:1.75;padding-left:9px;position:relative;text-transform:uppercase}
.expertise li::before{content:"";position:absolute;left:0;top:5px;width:4px;height:4px;background:var(--red)}
.expertise .btn-more{right:0;top:150px}

.sectors h2{position:absolute;left:18px;top:12px;width:726px;font-size:13px;font-weight:700;color:var(--red);text-transform:uppercase;padding-bottom:5px;border-bottom:1px solid var(--line)}
.sector-grid{position:absolute;left:18px;top:42px;width:726px;display:grid;grid-template-columns:repeat(4,168px);column-gap:18px;row-gap:16px}
.sector-card{height:152px;position:relative}
.sector-photo{height:86px;position:relative;border-radius:2px;overflow:hidden}
.sector-label{position:absolute;left:0;bottom:0;width:100%;height:18px;background:rgba(0,0,0,.6);color:var(--white);font-size:9px;font-weight:600;line-height:18px;padding-left:8px}
.sector-card p{font-size:7px;line-height:1.45;color:var(--grey);margin-top:6px}
.sector-card .btn-more{right:0;top:134px;height:14px;line-height:14px;font-size:6.5px;padding:0 8px}

.p-oil{background:linear-gradient(135deg,#e9963b,#b34a1b)}
.p-minerals{background:linear-gradient(135deg,#8a7a66,#3e3a36)}
.p-petro{background:linear-gradient(135deg,#8fb3d6,#2f5b88)}
.p-manufacturing{background:linear-gradient(135deg,#d98e3a,#6a2e12)}
.p-building{background:linear-gradient(135deg,#9cc6ea,#4c7fae)}
.p-telecom{background:linear-gradient(135deg,#3a6fbf,#0f2a5c)}
.p-rail{background:linear-gradient(135deg,#a9b0b8,#4a5058)}
.p-civil{background:linear-gradient(135deg,#d6a36a,#6b5540)}

/* footer */
.site-footer{position:absolute;left:0;top:1076px;width:828px;height:124px;background:var(--footer)}
.newsletter{position:absolute;left:33px;top:12px}
.newsletter h4{font-size:11px;font-weight:700;color:var(--white);text-transform:uppercase;margin-bottom:10px}
.news-input{width:210px;height:20px;background:#3a3a3a;border:1px solid #4a4a4a}
.news-btn{margin-top:8px;width:58px;height:17px;background:var(--red);color:var(--white);font-size:7.5px;font-weight:600;line-height:17px;text-align:center;border-radius:2px}
.social{position:absolute;right:33px;top:22px;display:flex;gap:5px}
.social span{width:16px;height:16px;border-radius:3px;background:#4a4a4a}
.social span:nth-child(1){background:#3b5998}
.social span:nth-child(2){background:#29a9e0}
.social span:nth-child(3){background:#0e76a8}
.social span:nth-child(4){background:#c4302b}
.social span:nth-child(5){background:#e68a2e}
.copyright{position:absolute;right:33px;top:48px;font-size:7px;color:#9a9a9a}
.footer-base{position:absolute;left:0;bottom:0;width:828px;height:14px;background:var(--footer-deep)}
</style>
</head>
<body>

<header class="site-header">
  <div class="brand">
    <span class="brand-dot"></span>
    <span class="brand-name">Brightwater Delivery Partners</span>
  </div>
  <div class="brand-tag">Providing Effective Project Controls and Management Solutions</div>
  <div class="contact">
    <div class="contact-row phone">
      <svg width="14" height="14" viewBox="0 0 24 24"><path fill="#c4161c" d="M6.6 10.8a15.1 15.1 0 0 0 6.6 6.6l2.2-2.2c.3-.3.7-.4 1-.2 1.1.4 2.3.6 3.6.6.6 0 1 .4 1 1V20c0 .6-.4 1-1 1A17 17 0 0 1 3 4c0-.6.4-1 1-1h3.5c.6 0 1 .4 1 1 0 1.3.2 2.5.6 3.6.1.3 0 .7-.2 1z"/></svg>
      +61 0400 555 123
    </div>
    <div class="contact-row mail">
      <svg width="12" height="9" viewBox="0 0 24 18"><rect x="1" y="1" width="22" height="16" rx="1" fill="none" stroke="#c4161c" stroke-width="2"/><path d="M1 1l11 9 11-9" fill="none" stroke="#c4161c" stroke-width="2"/></svg>
      info@brightwaterdeliverypartners-demo.com.au
    </div>
  </div>
</header>

<nav class="main-nav">
  <a class="active">Home</a>
  <a>About Us</a>
  <a>Expertise</a>
  <a>Knowledge</a>
  <a>Experience</a>
  <a>Projects</a>
  <a>Focus</a>
  <a>Contact</a>
  <a>Testimonials</a>
</nav>

<section class="hero" role="img" aria-label="Offshore oil drilling platform at dusk over the sea">
  <div class="hero-copy">
    <h2>Project Controls and Management Solutions</h2>
    <p>Our team brings clarity and control to complex projects, helping owners plan, track and deliver work across many sectors in Australia and overseas.</p>
  </div>
  <div class="hero-arrow prev"><svg width="10" height="10" viewBox="0 0 10 10"><path d="M7 1L3 5l4 4" fill="none" stroke="#fff" stroke-width="2"/></svg></div>
  <div class="hero-arrow next"><svg width="10" height="10" viewBox="0 0 10 10"><path d="M3 1l4 4-4 4" fill="none" stroke="#fff" stroke-width="2"/></svg></div>
</section>

<main class="content-zone">
  <section class="panel intro">
    <div class="welcome">
      <h1>Welcome to <span>Brightwater Delivery Partners</span></h1>
      <p>We provide services to companies in the mining and oil and gas sectors, enabling them to plan and manage their construction projects more effectively. This is achieved by reviewing their business practices and then implementing efficient tools and solutions that suit each team.</p>
      <p>Our clients are then able to plan and deliver their projects on time and within their budgets. We offer these services to both large and small companies within Australia and overseas, and we tailor every engagement to deliver proven value.</p>
      <span class="btn-more">View more »</span>
    </div>
    <aside class="expertise">
      <h3>Expertise</h3>
      <ul>
        <li>Project Management</li>
        <li>Project Controls</li>
        <li>Project Planning / Scheduling</li>
        <li>Cost Estimating Phases</li>
        <li>Systems Design and Implementation</li>
        <li>Resources</li>
        <li>Assisting Clients</li>
      </ul>
      <span class="btn-more">View more »</span>
    </aside>
  </section>

  <section class="panel sectors">
    <h2>We Serve</h2>
    <div class="sector-grid">
      <article class="sector-card">
        <div class="sector-photo p-oil" role="img" aria-label="Oil and gas refinery at sunset"><span class="sector-label">Oil &amp; Gas</span></div>
        <p>Planning and controls support for upstream and downstream oil and gas projects of every size.</p>
        <span class="btn-more">Read more</span>
      </article>
      <article class="sector-card">
        <div class="sector-photo p-minerals" role="img" aria-label="Mining machinery and mineral ore"><span class="sector-label">Minerals &amp; Metals</span></div>
        <p>Schedule and cost control for mine development, processing plants and site expansions.</p>
        <span class="btn-more">Read more</span>
      </article>
      <article class="sector-card">
        <div class="sector-photo p-petro" role="img" aria-label="Petrochemical plant towers against sky"><span class="sector-label">Petrochemical</span></div>
        <p>Integrated controls for plant builds, shutdowns and upgrades in petrochemical facilities.</p>
        <span class="btn-more">Read more</span>
      </article>
      <article class="sector-card">
        <div class="sector-photo p-manufacturing" role="img" aria-label="Manufacturing workshop with sparks"><span class="sector-label">Manufacturing</span></div>
        <p>Practical tools that help manufacturers plan capital works and track delivery clearly.</p>
        <span class="btn-more">Read more</span>
      </article>
      <article class="sector-card">
        <div class="sector-photo p-building" role="img" aria-label="Building under construction with cranes"><span class="sector-label">Building &amp; Construction</span></div>
        <p>Programme planning and reporting for commercial buildings and construction packages.</p>
        <span class="btn-more">Read more</span>
      </article>
      <article class="sector-card">
        <div class="sector-photo p-telecom" role="img" aria-label="Telecommunications tower and network lights"><span class="sector-label">Telecommunications</span></div>
        <p>Rollout scheduling and progress tracking for network and infrastructure programmes.</p>
        <span class="btn-more">Read more</span>
      </article>
      <article class="sector-card">
        <div class="sector-photo p-rail" role="img" aria-label="Modern train on a rail line"><span class="sector-label">Rail</span></div>
        <p>Controls and planning support for rail corridors, stations and rolling stock works.</p>
        <span class="btn-more">Read more</span>
      </article>
      <article class="sector-card">
        <div class="sector-photo p-civil" role="img" aria-label="Road works with heavy equipment"><span class="sector-label">Civil</span></div>
        <p>Cost and schedule control for roads, bridges, earthworks and civil infrastructure.</p>
        <span class="btn-more">Read more</span>
      </article>
    </div>
  </section>
</main>

<footer class="site-footer">
  <div class="newsletter">
    <h4>Newsletter</h4>
    <div class="news-input"></div>
    <div class="news-btn">Subscribe »</div>
  </div>
  <div class="social"><span></span><span></span><span></span><span></span><span></span></div>
  <div class="copyright">© 2013 Brightwater Delivery Partners. All rights reserved.</div>
  <div class="footer-base"></div>
</footer>

</body>
</html>
```